KRT Engineering Business Card Design

We’re looking for an elegant, clean, and timeless business card design that communicates experience, capability, and reliability.

KRT Engineering was established in 1995 , we are a Government Contracting company providing Professional Services to the Office of Frontier Affairs, Harbor Protection and the Vantage Collective. Our capabilities include: Acquisition & Program Management; Intelligence & Security Operations; Cyber, IT & Network Operations; Lifecycle Logistics & Asset Readiness; C5ISR Systems Engineering & Sustainment.

We want the card to reflect a straightforward, confident approach to business. The design should feel polished and professional without being flashy or overly corporate.

Design Direction
Clean, sophisticated, and uncluttered
Elegant but understated
Strong typography and thoughtful spacing
A timeless aesthetic rather than something overly trendy
Confident and established, with a sense of substance
Easy to read and practical in a real-world business setting

The overall impression should be: “These are experienced professionals who know what they’re doing, do what they say, and can be relied upon.”

We’re open to creative interpretations. The finished card should feel distinctive through its typography, proportions, layout, and attention to detail rather than through excessive graphics or visual effects.

We’re looking for a design that would make a potential client immediately feel that they’re dealing with a capable, trustworthy, and established company.

Company Colors: Navy and Gold/Yellow (but you do not need to use these colors on the card)
Company Name: KRT Engineering Associates, Inc. (known as KRT Engineering)
Website: krtengineering.com
Company Logo: Navy & Gold (other variations attached)

```html
<!DOCTYPE html>
<html lang="en">
<head>
<meta charset="utf-8">
<title>KRT Engineering – Business Card</title>
<link href="https://fonts.googleapis.com/css2?family=Roboto:wght@400;700;900&display=swap" rel="stylesheet">
<style>
  :root {
    --navy: #1f2a5e;
    --gold: #f2d84a;
    --paper: #f3f3f3;
    --ghost: #e2e3e8;
    --ink: #2a2a2a;
    --backdrop: #1b1b1b;
  }
  * { margin: 0; padding: 0; box-sizing: border-box; }
  html, body {
    width: 1200px;
    height: 1059px;
    overflow: hidden;
    background: var(--backdrop);
    font-family: "Roboto", Arial, sans-serif;
  }
  .card {
    position: absolute;
    width: 688px;
    height: 392px;
    border-radius: 20px;
    overflow: hidden;
  }
  .card-front {
    left: 257px;
    top: 89px;
    background: var(--paper);
    color: var(--ink);
  }
  .card-back {
    left: 254px;
    top: 547px;
    background: var(--navy);
    display: flex;
    align-items: center;
    justify-content: center;
  }
  .ghost-mark {
    position: absolute;
    right: -18px;
    top: 70px;
    font-weight: 900;
    font-size: 250px;
    line-height: 1;
    letter-spacing: -6px;
    color: var(--ghost);
  }
  .brand {
    position: absolute;
    left: 44px;
    top: 74px;
    display: flex;
    align-items: center;
    gap: 12px;
  }
  .brand-dot {
    width: 16px;
    height: 16px;
    border-radius: 50%;
    background: var(--gold);
  }
  .brand-name {
    font-weight: 900;
    font-size: 72px;
    line-height: 1;
    color: var(--navy);
    letter-spacing: -1px;
  }
  .brand-name--large {
    font-size: 120px;
    color: var(--paper);
    letter-spacing: -2px;
    margin-top: 30px;
  }
  .person {
    position: absolute;
    left: 47px;
    top: 198px;
  }
  .person-name {
    font-weight: 700;
    font-size: 24px;
    color: var(--navy);
    line-height: 1.2;
  }
  .person-title {
    font-size: 17.5px;
    line-height: 1.3;
    color: var(--ink);
  }
  .contacts {
    position: absolute;
    left: 47px;
    top: 262px;
    list-style: none;
  }
  .contact {
    display: flex;
    align-items: center;
    gap: 9px;
    height: 31px;
    font-size: 18.5px;
    color: var(--ink);
  }
  .contact-icon {
    width: 14px;
    height: 14px;
    fill: var(--navy);
    flex: none;
  }
</style>
</head>
<body>
  <section class="card card-front" aria-label="Business card front">
    <span class="ghost-mark" aria-hidden="true">KRT</span>
    <div class="brand">
      <span class="brand-name">KRT</span>
      <span class="brand-dot"></span>
    </div>
    <div class="person">
      <p class="person-name">Megan R. Callahan</p>
      <p class="person-title">Principal Engineer</p>
    </div>
    <ul class="contacts">
      <li class="contact">
        <svg class="contact-icon" viewBox="0 0 24 24" aria-hidden="true"><path d="M6.6 10.8a15.1 15.1 0 0 0 6.6 6.6l2.2-2.2a1 1 0 0 1 1-.25 11.4 11.4 0 0 0 3.6.57 1 1 0 0 1 1 1V20a1 1 0 0 1-1 1A17 17 0 0 1 3 4a1 1 0 0 1 1-1h3.5a1 1 0 0 1 1 1c0 1.25.2 2.45.57 3.57a1 1 0 0 1-.25 1z"/></svg>
        <span>(555) 987-2140</span>
      </li>
      <li class="contact">
        <svg class="contact-icon" viewBox="0 0 24 24" aria-hidden="true"><path d="M2 9l10-7 10 7v12H2zm2 1.2V19h16v-8.8l-8 5.6z"/></svg>
        <span>m.c@krtengineering.com</span>
      </li>
      <li class="contact">
        <svg class="contact-icon" viewBox="0 0 24 24" aria-hidden="true"><path d="M12 2a10 10 0 1 0 0 20 10 10 0 0 0 0-20zm-1 17.9A8 8 0 0 1 4.2 10.2L9 15v1a2 2 0 0 0 2 2zm6.9-2.5A2 2 0 0 0 16 16h-1v-3a1 1 0 0 0-1-1H8v-2h2a1 1 0 0 0 1-1V7h2a2 2 0 0 0 2-2v-.4a8 8 0 0 1 2.9 12.8z"/></svg>
        <span>krtengineering.com</span>
      </li>
    </ul>
  </section>

  <section class="card card-back" aria-label="Business card back">
    <span class="brand-name brand-name--large">KRT</span>
  </section>
</body>
</html>
```